Design a compelling Tarnwove Business Card that will drive people to my site

I want a business card that I can give to people—less to tell them who I am and more to direct them to my website. My website is a portal for Pelmor Aquatics Officials and a place for people who want to become Pelmor Aquatics Officials.
I am uploading my official company logo as well as a business card mockup that I did on my own. Please feel free to completely stray from this design.
I've included a screen recording of the homepage of my website as well.
Target Market(s)
Pelmor Aquatics Officials and people who desire to become one
Contact Information for Business Card
website url
Look and feel
Each slider illustrates characteristics of the customer's brand and the style your logo design should communicate.

```html
<!DOCTYPE html>
<html lang="en">
<head>
<meta charset="utf-8">
<title>Tarnwove Business Card</title>
<link rel="stylesheet" href="https://fonts.googleapis.com/css2?family=Montserrat:wght@500;600;700&display=swap">
<style>
  :root {
    --stage: #d9d9d9;
    --brand-blue: #3a55a6;
    --soft-blue: #93a8d6;
    --paper: #ffffff;
    --name-blue: #9fb3e2;
  }
  * { margin: 0; padding: 0; box-sizing: border-box; }
  html, body { width: 1200px; height: 802px; overflow: hidden; }
  body {
    background: var(--stage);
    font-family: "Montserrat", Arial, sans-serif;
    position: relative;
  }
  .card {
    position: absolute;
    top: 252px;
    width: 520px;
    height: 297px;
    border-radius: 22px;
    overflow: hidden;
  }
  .card--front { left: 60px; background: var(--paper); }
  .card--back { left: 620px; background: var(--brand-blue); }
  .card__wave { position: absolute; inset: 0; width: 100%; height: 100%; }
  .wordmark {
    position: absolute;
    font-weight: 700;
    letter-spacing: -1px;
    line-height: 1;
    white-space: nowrap;
  }
  .card--front .wordmark {
    left: 28px; top: 112px;
    font-size: 37px;
    color: var(--brand-blue);
  }
  .card--back .wordmark {
    left: 0; right: 0; top: 118px;
    text-align: center;
    font-size: 72px;
    color: var(--paper);
  }
  .contact {
    position: absolute;
    right: 30px; top: 52px;
    text-align: right;
    color: var(--paper);
  }
  .contact__name {
    font-size: 20px; font-weight: 700;
    color: var(--name-blue);
  }
  .contact__title { font-size: 13px; font-weight: 500; margin-top: 3px; }
  .contact__rule {
    width: 14px; height: 1px; background: var(--paper);
    margin: 10px 0 10px auto; opacity: .8;
  }
  .contact__list { list-style: none; font-size: 13px; font-weight: 500; }
  .contact__list li {
    display: flex; align-items: center; justify-content: flex-end;
    gap: 7px; margin-bottom: 6px;
  }
  .contact__icon { width: 11px; height: 11px; flex: none; }
</style>
</head>
<body>
  <section class="card card--front" aria-label="Business card front">
    <svg class="card__wave" viewBox="0 0 520 297" aria-hidden="true">
      <path d="M0,222 C170,216 250,150 290,90 C325,36 350,8 392,2" fill="none" stroke="var(--soft-blue)" stroke-width="9"/>
      <path d="M0,236 C180,230 262,162 302,100 C336,46 362,14 402,0 L520,0 L520,297 L0,297 Z" fill="var(--brand-blue)"/>
    </svg>
    <div class="wordmark">tarnwove</div>
    <div class="contact">
      <div class="contact__name">Marcus Ellery</div>
      <div class="contact__title">CEO &amp; Founder</div>
      <div class="contact__rule"></div>
      <ul class="contact__list">
        <li>(555) 210-4471
          <svg class="contact__icon" viewBox="0 0 12 12" aria-hidden="true"><path d="M3 1 L5 3.5 L3.8 4.8 C4.5 6.3 5.7 7.5 7.2 8.2 L8.5 7 L11 9 L9.6 10.8 C5 10.5 1.5 7 1.2 2.4 Z" fill="var(--paper)"/></svg>
        </li>
        <li>marcus@tarnwove.com
          <svg class="contact__icon" viewBox="0 0 12 12" aria-hidden="true"><rect x="1" y="2.5" width="10" height="7" fill="var(--paper)"/><path d="M1 2.5 L6 6.5 L11 2.5" fill="none" stroke="var(--brand-blue)" stroke-width="1"/></svg>
        </li>
        <li>www.tarnwove.com
          <svg class="contact__icon" viewBox="0 0 12 12" aria-hidden="true"><circle cx="6" cy="6" r="5" fill="none" stroke="var(--paper)" stroke-width="1.2"/><ellipse cx="6" cy="6" rx="2.2" ry="5" fill="none" stroke="var(--paper)" stroke-width="1"/><path d="M1 6 H11" stroke="var(--paper)" stroke-width="1"/></svg>
        </li>
      </ul>
    </div>
  </section>

  <section class="card card--back" aria-label="Business card back">
    <div class="wordmark">tarnwove</div>
  </section>
</body>
</html>
```